Indy Film Production Company/Studio

We need a business card designed from an existing logo. We are a digital studio/production company that caters to creating genre entertainment, like Action, Horror, and martial arts. The card along with the logo will be used to Brand the company from letter heads to banners. The design will also be used for postcards and Brochures. It should be professional and masculine.
Updates

Thank you to all the designers who have participated. I'm narrowing down who it will be. Thank you again.

Target Market(s)

Investors, Networks, Producers, and actors

Industry/Entity Type

Film Production

Contact Information for Business Card

Teodoro Valbuena
Producer/Writer/Director
www.kestrelpicturehouse.example

Requirements
Must have
• Website address, Facebook icon and Twitter icon possibly in the back of the card.
Nice to have
• Logline of Company: Follow The Action.

```html
<!DOCTYPE html>
<html lang="en">
<head>
<meta charset="utf-8">
<title>Kestrel Picture House – Business Card</title>
<link href="https://fonts.googleapis.com/css2?family=Roboto:wght@400;700;900&display=swap" rel="stylesheet">
<style>
  :root {
    --stage: #e9e6e1;
    --card-white: #ffffff;
    --brand-red: #e8202a;
    --ink-dark: #1c1c1c;
    --ink-light: #ffffff;
  }
  * { margin: 0; padding: 0; box-sizing: border-box; }
  html, body {
    width: 1200px; height: 950px; overflow: hidden;
    background: var(--stage);
    font-family: "Roboto", Arial, sans-serif;
  }
  .sheet {
    width: 1200px; height: 950px;
    display: flex; flex-direction: column; align-items: center; justify-content: center;
    gap: 50px;
  }
  .card {
    position: relative;
    width: 700px; height: 400px;
    overflow: hidden;
    box-shadow: 0 6px 18px rgba(0,0,0,0.18);
  }
  .card--front { background: var(--card-white); }
  .card--back { background: var(--brand-red); color: var(--ink-light); }

  .social {
    position: absolute; top: 18px; right: 18px;
    display: flex; gap: 3px;
  }
  .social__tile {
    width: 22px; height: 22px;
    background: var(--ink-dark);
    display: flex; align-items: center; justify-content: center;
  }
  .social__tile svg { width: 13px; height: 13px; }

  .wordmark {
    font-weight: 900;
    text-transform: uppercase;
    letter-spacing: 1px;
    line-height: 1;
  }
  .card--front .wordmark {
    position: absolute; left: 0; right: 0; top: 178px;
    text-align: center; font-size: 40px; color: var(--brand-red);
  }
  .card--back .wordmark {
    position: absolute; right: 40px; top: 90px;
    font-size: 34px; color: var(--ink-light); text-align: right;
  }

  .rule-top {
    position: absolute; left: 40px; right: 40px; top: 150px;
    border-top: 1px solid rgba(255,255,255,0.75);
  }

  .identity {
    position: absolute; left: 40px; right: 40px; bottom: 90px;
    font-size: 20px;
    border-bottom: 1px solid rgba(255,255,255,0.75);
    padding-bottom: 10px;
  }
  .identity__name { font-weight: 700; }
  .identity__role { font-weight: 400; }

  .contacts {
    position: absolute; left: 40px; right: 40px; bottom: 48px;
    display: flex; justify-content: space-between; align-items: center;
    font-size: 13px;
  }
  .contact { display: flex; align-items: center; gap: 6px; white-space: nowrap; }
  .contact svg { width: 14px; height: 14px; flex: none; }
</style>
</head>
<body>
<main class="sheet">

  <section class="card card--front" aria-label="Card front">
    <div class="social" aria-label="Social profiles">
      <span class="social__tile" aria-label="Social profile">
        <svg viewBox="0 0 16 16" aria-hidden="true"><path d="M2 3h12v8H7l-3 3v-3H2z" fill="none" stroke="#fff" stroke-width="1.6" stroke-linejoin="round"/></svg>
      </span>
      <span class="social__tile" aria-label="Social profile">
        <svg viewBox="0 0 16 16" aria-hidden="true"><path d="M7 9.5l2-3M6 5l1.5-1.5a2.5 2.5 0 0 1 3.5 3.5L9.5 8.5M10 11l-1.5 1.5A2.5 2.5 0 0 1 5 9l1.5-1.5" fill="none" stroke="#fff" stroke-width="1.6" stroke-linecap="round"/></svg>
      </span>
    </div>
    <p class="wordmark">Kestrel Picture House</p>
  </section>

  <section class="card card--back" aria-label="Card back">
    <p class="wordmark">Kestrel Picture House</p>
    <div class="rule-top"></div>

    <p class="identity">
      <span class="identity__name">Teodoro Valbuena</span>
      <span class="identity__role"> - Producer/Writer/Director</span>
    </p>

    <div class="contacts">
      <span class="contact">
        <svg viewBox="0 0 16 16" aria-hidden="true"><path fill="#fff" d="M3 1h3l1 4-2 1.5c.8 1.8 2.2 3.2 4 4L10.5 8.5l4 1v3c0 1-1 2-2 2C6.5 14.5 1.5 9.5 1.5 3c0-1 .5-2 1.5-2z"/></svg>
        555 014 7788
      </span>
      <span class="contact">
        <svg viewBox="0 0 16 16" aria-hidden="true"><path d="M1 3h14v10H1z M1.5 3.5 8 9l6.5-5.5" fill="none" stroke="#fff" stroke-width="1.4"/></svg>
        teo@kestrelpicturehouse.example
      </span>
      <span class="contact">
        <svg viewBox="0 0 16 16" aria-hidden="true"><circle cx="8" cy="8" r="6.5" fill="none" stroke="#fff" stroke-width="1.4"/><path d="M1.5 8h13M8 1.5c2.5 3 2.5 10 0 13M8 1.5c-2.5 3-2.5 10 0 13" fill="none" stroke="#fff" stroke-width="1.2"/></svg>
        www.kestrelpicturehouse.example
      </span>
    </div>
  </section>

</main>
</body>
</html>
```